Residential improvers, A Quiet Harbor 9 Z *

Quiet Harbor 9 Z is a real estate company specializing in turning unloved properties into improved, happy places to live. We specialize in thoughtfully-improved residential properties for buyers or renters. Our company needs a business card that reflects the renovated homes we create using green and Feng Shui principles,

Please disregard the images we submitted. We are looking for an abstract, sophisticated elegant design. No eggs in a nest ... nothing cute. The image can be soft.
Updates

Aloha (hello) all designers. We are a serious property investment/improvement company. We strive to be unique, renovating with style and elegance. Our business card must portray the same message. We thought the nest and flower might be "it" ... clearly it's not, once we saw what you submitted. Please revisit the brief as it was modified yesterday. Mahalo for your input! We look forward to hearing from all designers that have been invited.

Industry/Entity Type

Real Estate Development

Contact Information for Business Card

We will have separate business cards for
1) Corabeth Dunmore 555-310-7290 corabeth@mailvista.test
2) Tessa Harwick 555-347-6152 tessaharwick@mailvista.test
** can we add the website later ... in the process of approval.
Investors * Renovators * Connectors

Font styles to use
Sans Serif

Colors
cadf82

Requirements
Must have
• a feng shui feel ... modern. Color - green with black print.
Nice to have
• A Quiet Harbor 9 Z

```html
<!DOCTYPE html>
<html lang="en">
<head>
<meta charset="utf-8">
<title>A Quiet Harbor 9 Z — Business Card</title>
<link rel="stylesheet" href="https://fonts.googleapis.com/css2?family=Montserrat:wght@500;600;700&display=swap">
<style>
  :root {
    --page: #d9d6d0;
    --card: #f4f4f1;
    --ink: #1d1d1b;
    --green: #cadf82;
    --green-deep: #86b64a;
    --green-dot: #9cc656;
  }
  * { margin: 0; padding: 0; box-sizing: border-box; }
  html, body { width: 1200px; height: 970px; overflow: hidden; background: var(--page); }
  body { font-family: "Montserrat", sans-serif; color: var(--ink); position: relative; }

  .card {
    position: absolute; left: 60px; top: 178px;
    width: 1080px; height: 613px;
    background: var(--card);
    border-radius: 30px;
    overflow: hidden;
    box-shadow: 0 10px 30px rgba(0,0,0,.18);
  }

  .card__backdrop {
    position: absolute; left: 0; right: 0; bottom: 0; height: 360px;
    background:
      linear-gradient(to bottom, rgba(244,244,241,1) 0%, rgba(244,244,241,0) 55%),
      linear-gradient(90deg, var(--green) 0%, #a9cc62 55%, var(--green-deep) 100%);
  }

  .services { position: absolute; right: 50px; top: 68px; list-style: none; text-align: right; }
  .services li { font-size: 24px; font-weight: 600; line-height: 33px; display: flex; justify-content: flex-end; align-items: center; gap: 12px; }
  .services li::after { content: ""; width: 12px; height: 12px; border-radius: 50%; background: var(--green-dot); }

  .brand { position: absolute; left: 66px; top: 272px; display: flex; align-items: center; gap: 14px; }
  .brand__mark { width: 26px; height: 26px; border-radius: 50%; background: var(--green-deep); }
  .brand__name { font-size: 38px; font-weight: 600; letter-spacing: -0.3px; color: var(--ink); }

  .contact { position: absolute; right: 48px; top: 408px; text-align: right; }
  .contact__name { font-size: 29px; font-weight: 700; margin-bottom: 20px; }
  .contact__line { display: flex; justify-content: flex-end; align-items: center; gap: 10px; font-size: 23px; font-weight: 500; height: 34px; }
  .contact__icon { width: 30px; height: 30px; }
</style>
</head>
<body>
  <section class="card" aria-label="Business card for A Quiet Harbor 9 Z">
    <div class="card__backdrop" role="img" aria-label="Soft green flowing wave artwork across the lower part of the card"></div>

    <ul class="services">
      <li>Investors</li>
      <li>Renovators</li>
      <li>Connectors</li>
    </ul>

    <div class="brand">
      <span class="brand__mark"></span>
      <span class="brand__name">A Quiet Harbor 9 Z</span>
    </div>

    <div class="contact">
      <p class="contact__name">Corabeth Dunmore</p>
      <p class="contact__line">555-310-7290
        <svg class="contact__icon" viewBox="0 0 30 30" aria-hidden="true"><circle cx="15" cy="15" r="13" fill="none" stroke="#1d1d1b" stroke-width="2"/><rect x="10.5" y="7.5" width="9" height="15" rx="1.5" fill="none" stroke="#1d1d1b" stroke-width="1.8"/></svg>
      </p>
      <p class="contact__line">corabeth@mailvista.test
        <svg class="contact__icon" viewBox="0 0 30 30" aria-hidden="true"><circle cx="15" cy="15" r="13" fill="none" stroke="#1d1d1b" stroke-width="2"/><rect x="8" y="10" width="14" height="10" rx="1" fill="#1d1d1b"/><path d="M8 10 L15 16 L22 10" fill="none" stroke="#f4f4f1" stroke-width="1.3"/></svg>
      </p>
      <p class="contact__line">www.quietharbor9z.test
        <svg class="contact__icon" viewBox="0 0 30 30" aria-hidden="true"><circle cx="15" cy="15" r="13" fill="none" stroke="#1d1d1b" stroke-width="2"/><circle cx="15" cy="15" r="8" fill="none" stroke="#1d1d1b" stroke-width="1.5"/><ellipse cx="15" cy="15" rx="3.5" ry="8" fill="none" stroke="#1d1d1b" stroke-width="1.3"/><path d="M7 15 H23" stroke="#1d1d1b" stroke-width="1.3"/></svg>
      </p>
    </div>
  </section>
</body>
</html>
```